Rice Cakes Packing Desing

We need a simple (4 color) yet colorful, atractive design for a Rice Cake polypropylene bag. We are expanding our line to include 8-10 different flavors with each bag being a different color for easy identificaction. We are starting right with the first design. We already have "sample model" (of an existing product in the usa market) upon which we believe that our design could be based on (as an idea of a simple 4 color plastic bag design), which we are including in this post. We are also including an image of Brindle Rice Cakes plastic bag that has a round front window that shows the product inside the bag, which we also would like to include in our design. We already have a brand name and a logo design. The bag's dimension is about 20cms (wide) 30cms (tall) and it will contain about 12 rice cakes inside. (I HAVE ATTACHED A COUPLE OF IMAGES OF A PRINTED POLYPROPYLENE RICE CAKES BAG FOR YOUR REFERENCE)
Updates

Project Deadline Extended
Reason: We want to provide the designers with NUTRITIONAL INFORMATION, Bar Code, Company information, Ingredients, important pointers, etc. to be incorporated into the design. We would like to provide a few more days in order to fully integrate the back & front text into the package design in order to attain a perfectly balanced and well presented package. So far we have received some very interesting and highly viable proposals and we would like to provide the designers the necessary text information in order to have a complete, fully designed, great-looking package. We feel that with the extension the final design can be completed and we can have an opportunity to review, incorporate/change/modify any details before choosing the final design. Great designs have been submitted and we will definitely choose one before the newly proposed deadline. Thanks to all!

Target Market(s)

Although the concept of RICE CAKES might very well have its origins in ASIA the idea is to create a design (logo & pack) that will convey a message to the end consumer that our brand name stands for "FRESHNESS", "HEALTHY", "NATURE'S BEST", "TOP GRAINS", "GOODNESS", in short if you consume are products "IT IS GOOD FOR YOU!" (not only for people who love oriental food). We would like to have a product image that says "Hey! This looks Healthy & Tasty" (non-fattening, yummy and good!)

When you buy a pack of GRANOLAS what do you think about? What do you believe it is that you are buying? Good, Healthy Stuff? Good Tasting? Good for you? That's the idea!

Besides Rice Cakes are super light, fluffy, crunchy and easy to digest that it makes it a great Snack for everyone! Kids & Adults!

We need the full complete design of the actual bag (where the Rice Cakes will be packed) in order to start production of the bags right.

Industry/Entity Type

Plastic

Requirements
Must have
• We already have a local company in Mexico City that makes printed polypropylene bags. They are only waiting for the bag design in order to print the 20cms x 30cms bags.
Kindly consider that on the back Nutritional Information will be needed as well as a BarCode, company information, some bullets (pointing to the most important benefits of the product), etc. We will provide all the text information.
Nice to have
• Kindly take a look at the newly uploaded images from "TORVE" Rice Cake packages. They are a good example of how to accomplish a great looking design using only 4 colors (which saves a lot in printing costs)
Should not have
• We do NOT want to have a design that says "This is ORIENTAL food". We don't want it to appear like "Sushi Rice" or "Japanese food", etc.

```html
<!DOCTYPE html>
<html lang="en">
<head>
<meta charset="utf-8">
<title>Oakfield Foods Rice Cakes – Lightly Salted Bag Front</title>
<link href="https://fonts.googleapis.com/css2?family=Great+Vibes&family=Cormorant+Garamond:ital,wght@1,600&family=Lato:wght@400;700;900&family=Roboto+Condensed:wght@700&display=swap" rel="stylesheet">
<style>
  :root {
    --leaf-green: #b9d562;
    --sand: #dfbb9b;
    --gold-line: #c9a25a;
    --paper: #f1f0e9;
    --cocoa: #6b3b22;
    --slate: #6d6c6a;
    --white: #ffffff;
    --wheat-light: #f4c96a;
    --wheat-deep: #b5731c;
    --window-light: #ece6da;
    --window-deep: #cfc4b1;
  }
  * { margin: 0; padding: 0; box-sizing: border-box; }
  html, body { width: 800px; height: 1200px; overflow: hidden; background: var(--white); }
  .bag { position: relative; width: 800px; height: 1200px; overflow: hidden; background: var(--white); }

  .top-band { position: absolute; left: 0; top: 37px; width: 800px; height: 237px; background: var(--leaf-green); }

  .brand-band {
    position: absolute; left: 0; top: 274px; width: 800px; height: 127px;
    background: var(--sand);
    border-top: 3px solid var(--gold-line);
    border-bottom: 3px solid var(--gold-line);
  }
  .brand-band .tag {
    position: absolute; top: 48px;
    font-family: "Lato", sans-serif; font-weight: 400; font-size: 22px;
    letter-spacing: 0.5px; color: var(--white);
  }
  .brand-band .tag--left { left: 35px; }
  .brand-band .tag--right { right: 42px; }

  .brand-mark {
    position: absolute; left: 400px; top: 208px; transform: translateX(-50%);
    display: flex; flex-direction: column; align-items: center; gap: 18px;
  }
  .brand-mark .seal {
    width: 116px; height: 116px; border-radius: 50%;
    background: var(--white); border: 3px solid var(--gold-line);
  }
  .brand-mark .brand-name {
    font-family: "Lato", sans-serif; font-weight: 900; font-size: 36px;
    color: var(--white); white-space: nowrap; letter-spacing: 0.5px; line-height: 1;
  }

  .paper-panel { position: absolute; left: 0; top: 401px; width: 800px; height: 491px; background: var(--paper); }

  .flavour {
    position: absolute; left: 0; width: 800px; top: 414px; text-align: center;
    font-family: "Cormorant Garamond", serif; font-style: italic; font-weight: 600;
    font-size: 64px; color: var(--cocoa); padding-right: 20px;
  }

  .grain-art {
    position: absolute; left: 0; top: 500px; width: 460px; height: 370px;
    background: radial-gradient(ellipse at 65% 70%, #ffffff 0%, #e6e1d4 35%, rgba(214,170,110,0.55) 65%, rgba(241,240,233,0) 85%);
  }

  .benefits {
    position: absolute; left: 578px; top: 507px; width: 210px;
    border-left: 1px solid #b7b5b0; list-style: none;
  }
  .benefits li {
    position: relative; padding-left: 10px; height: 39px; line-height: 39px;
    font-family: "Roboto Condensed", sans-serif; font-weight: 700; font-size: 15px;
    color: var(--slate); white-space: nowrap;
  }
  .benefits li::before {
    content: ""; position: absolute; left: -3px; top: 17px;
    width: 5px; height: 5px; border-radius: 50%; background: #9e9c97;
  }

  .claim-band { position: absolute; left: 0; top: 880px; width: 800px; height: 66px; background: var(--leaf-green); }
  .claim-band .claim {
    position: absolute; left: 88px; top: 14px;
    font-family: "Lato", sans-serif; font-weight: 400; font-size: 30px;
    letter-spacing: 1.5px; color: var(--white);
  }

  .field-art {
    position: absolute; left: 0; top: 946px; width: 800px; height: 254px;
    background: linear-gradient(100deg, var(--wheat-deep) 0%, var(--wheat-light) 30%, #d99a36 55%, var(--wheat-deep) 80%, #8e5514 100%);
  }

  .product-name { position: absolute; left: 0; top: 0; font-family: "Great Vibes", cursive; font-weight: 400; color: var(--white); line-height: 1; }
  .product-name .line-rice { position: absolute; left: 100px; top: 932px; font-size: 128px; }
  .product-name .line-cakes { position: absolute; left: 76px; top: 982px; font-size: 196px; }

  .net-weight {
    position: absolute; right: 64px; top: 1124px;
    font-family: "Lato", sans-serif; font-weight: 400; font-size: 22px; color: var(--white);
  }

  .window {
    position: absolute; left: 413px; top: 743px; width: 328px; height: 328px;
    border-radius: 50%; border: 8px solid var(--white); overflow: hidden;
    background: radial-gradient(circle at 45% 40%, var(--window-light) 0%, var(--window-deep) 100%);
  }
</style>
</head>
<body>
<main class="bag">
  <div class="top-band"></div>

  <header class="brand-band">
    <span class="tag tag--left">NATURE'S BEST</span>
    <span class="tag tag--right">12 RICE CAKES</span>
  </header>

  <div class="brand-mark">
    <span class="seal"></span>
    <span class="brand-name">OAKFIELD FOODS</span>
  </div>

  <section class="paper-panel"></section>

  <h2 class="flavour">Lightly salted</h2>

  <div class="grain-art" role="img" aria-label="Golden wheat stalks beside a tipped bowl spilling white salt"></div>

  <ul class="benefits">
    <li>30 CALORIES PER SLICE</li>
    <li>NATURAL INGREDIENTS</li>
    <li>NO TRANS FAT</li>
    <li>NO PRESERVATIVES</li>
    <li>NO FOOD COLORS</li>
    <li>WHOLE GRAIN</li>
  </ul>

  <div class="claim-band"><span class="claim">GLUTEN FREE</span></div>

  <div class="field-art" role="img" aria-label="Sunlit golden wheat field"></div>

  <h1 class="product-name">
    <span class="line-rice">rice</span>
    <span class="line-cakes">cakes</span>
  </h1>

  <p class="net-weight">NET WT 3.5 OZ {100gr}</p>

  <div class="window" role="img" aria-label="Round clear window showing the rice cakes packed inside the bag"></div>
</main>
</body>
</html>
```